Restaurant Menu New Design

Hello Designers,

Blue Fern is a casual family oriented dine-in restaurant, we serve American Italian dishes like Pizza, Pasta, and Sandwiches.

We are excited about adding some new delicious dishes and recipes to our menu. And we are looking for a talented and creative designer to design it.

The menu is a 12 page black leather book, page size is:
6.5" X 11.69" (16.51 cm X 29.69 cm)

Below is the scope of work and requirements:

1) Design a completely all new, creative, and beautiful menu, including cover page, blue fern oven intro. page, interior pages, and kids menu page.

2) Design a take out edition of the menu. It will be exactly the same as the dine-in menu, but with the addition of a back cover page with info such as contacts, social media, location map, etc…

3) Files are required in Adobe Illustrator format. Layers should be organized, all text should be editable, and all the food pictures easy to change.

4) This is a two language menu, so you are required to make space in the design for a second language. The easiest way to do that is have every item listed in English twice, then I will edit the second text with Illustrator.

5) In your initial design submission, the minimum you are required to submit are these 4 pages:
– Cover page
– Typical interior menu page
– Kids menu page
– Take-out menu back cover page

If your initial design is selected, then you are required to submit all remaining pages to complete the project.

In the link below, you will find:
1) Logo
2) New menu text in Excel
3) Food images (will take some time to upload)
4) The old dine-in and take out menu designs

https://www.filevaultra.com/sh/kq7tmwzabe3pxd/BBBrTnpLk41QaWmZpQ8V2X7Jd?dl=0

Thank you for stopping by and reading this brief. I hope you like this project and enjoy designing our new menu. Please let me know if you have any questions.

Cheers!

Project Deadline Extended
Reason: We have decided to extend the deadline due to the low number of submissions which was much lower than the expected submissions we were give by Brief Harbor.

```html
<!DOCTYPE html>
<html lang="en">
<head>
<meta charset="utf-8">
<title>Blue Fern — Pasta</title>
<link href="https://fonts.googleapis.com/css2?family=Lato:wght@300;400;700&family=Noto+Sans+Arabic:wght@300;400&display=swap" rel="stylesheet">
<style>
  :root{
    --board:#343436;
    --line:#d9d9d9;
    --title:#ffffff;
    --copy:#a9a9ab;
    --doodle:#4a4a4d;
    --plate:#f3f1ee;
  }
  html,body{margin:0;padding:0;background:var(--board);overflow:hidden;}
  .menu-page{position:relative;width:670px;height:1200px;background:var(--board);overflow:hidden;font-family:"Lato",sans-serif;}
  .abs{position:absolute;}
  .section-head{position:absolute;top:36px;width:120px;text-align:center;color:var(--title);font-size:21px;font-weight:400;letter-spacing:.5px;}
  .rule{position:absolute;background:var(--line);height:1px;}
  .vrule{position:absolute;background:var(--line);width:1px;}
  .doodle{position:absolute;background:var(--doodle);border-radius:10px;opacity:.55;}
  .dish{position:absolute;text-align:center;}
  .dish-name{color:var(--title);font-weight:700;font-size:13.5px;line-height:17px;letter-spacing:.2px;margin:0;}
  .dish-name .ar{font-family:"Noto Sans Arabic",sans-serif;font-weight:400;}
  .dish-copy{color:var(--copy);font-weight:300;font-size:12px;line-height:15.5px;margin:6px 0 0;}
  .dish-copy.small{font-size:9.5px;line-height:12px;}
  .dish-ar{color:var(--copy);font-family:"Noto Sans Arabic",sans-serif;font-weight:300;font-size:11.5px;line-height:15.5px;margin:8px 0 0;direction:rtl;}
  .dish-ar.small{font-size:9.5px;line-height:13px;}
  .photo{position:absolute;}
</style>
</head>
<body>
<main class="menu-page">

  <!-- headers -->
  <h1 class="section-head" style="left:122px;margin:0;">PASTA</h1>
  <h1 class="section-head" style="left:440px;margin:0;">PASTA</h1>
  <div class="rule" style="left:4px;top:69px;width:176px;"></div>
  <div class="rule" style="left:468px;top:69px;width:198px;"></div>
  <div class="doodle" role="img" aria-label="Line drawing of a serving cloche" style="left:300px;top:36px;width:74px;height:48px;"></div>
  <div class="doodle" role="img" aria-label="Line drawings of tomato, cheese wedge and pepper" style="left:136px;top:80px;width:96px;height:32px;"></div>
  <div class="doodle" role="img" aria-label="Line drawings of peas, herb sprig and mushrooms" style="left:424px;top:84px;width:132px;height:32px;"></div>

  <!-- Fettuccine Alfredo -->
  <section class="dish" style="left:62px;top:142px;width:240px;">
    <h2 class="dish-name">FETTUCCINE ALFREDO|<br><span class="ar">فيتوتشيني ألفريدو</span></h2>
    <p class="dish-copy" style="margin-top:14px;">Fettuccine with creamy white sauce<br>&amp; parmesan cheese&nbsp; 27<br>with chicken 37, with shrimp 42</p>
    <p class="dish-ar" style="margin-top:14px;">فيتوتشيني مع صوص الكريمة<br>وجبنة البارميجان 32<br>مع الدجاج 42، مع الجمبري 47</p>
  </section>
  <div class="doodle" role="img" aria-label="Line drawing of a wheat stalk" style="left:296px;top:140px;width:40px;height:72px;"></div>
  <div class="doodle" role="img" aria-label="Line drawing of a tomato" style="left:326px;top:256px;width:32px;height:32px;"></div>
  <div class="doodle" role="img" aria-label="Line drawing of a leaf" style="left:286px;top:296px;width:56px;height:48px;"></div>

  <!-- Lasagna -->
  <section class="dish" style="left:62px;top:322px;width:240px;">
    <h2 class="dish-name">LASAGNA | <span class="ar">لازانيا</span></h2>
    <p class="dish-copy" style="margin-top:13px;">Layers of pasta, beef bolognese,<br>bechamel sauce, topped with melted<br>mozzarella&nbsp; 35</p>
    <p class="dish-ar" style="margin-top:15px;">طبقات من الباستا مع صلصة<br>البولونيز والبيشاميل ومغطاة<br>بالموزاريلا السائحة 35</p>
  </section>
  <div class="doodle" role="img" aria-label="Line drawing of a cutting board" style="left:308px;top:382px;width:52px;height:54px;"></div>

  <!-- photo: spaghetti bolognese -->
  <div class="vrule" style="left:362px;top:134px;height:74px;"></div>
  <div class="rule" style="left:362px;top:134px;width:82px;"></div>
  <div class="photo" role="img" aria-label="Photo of spaghetti bolognese on a white plate with garlic bread" style="left:372px;top:146px;width:236px;height:157px;background:radial-gradient(ellipse 46% 34% at 46% 62%, #8a3a1f 0 45%, var(--plate) 47% 72%, #2a2320 76%),#2a2320;"></div>
  <div class="vrule" style="left:628px;top:180px;height:136px;"></div>
  <div class="rule" style="left:552px;top:316px;width:77px;"></div>

  <!-- Spaghetti Bolognese -->
  <section class="dish" style="left:378px;top:332px;width:224px;">
    <h2 class="dish-name" style="font-weight:400;">SPAGHETTI BOLOGNESE |<br><span class="ar">سباجيتي بولونيز</span></h2>
    <p class="dish-copy small" style="margin-top:7px;">Spaghetti with beef bolognese sauce&nbsp; 33</p>
    <p class="dish-ar small" style="margin-top:11px;">سباجيتي مع صلصة بولونيز باللحم 33</p>
  </section>
  <div class="doodle" role="img" aria-label="Line drawings of garlic and peas" style="left:460px;top:424px;width:84px;height:32px;"></div>

  <!-- divider -->
  <div class="rule" style="left:0;top:478px;width:670px;"></div>
  <div class="doodle" role="img" aria-label="Line drawing of a rolling pin" style="left:280px;top:470px;width:140px;height:16px;opacity:.9;"></div>

  <!-- photo: penne -->
  <div class="rule" style="left:42px;top:494px;width:186px;"></div>
  <div class="vrule" style="left:42px;top:494px;height:122px;"></div>
  <div class="rule" style="left:52px;top:503px;width:176px;"></div>
  <div class="photo" role="img" aria-label="Photo of penne in tomato sauce in a white bowl" style="left:64px;top:514px;width:236px;height:156px;background:radial-gradient(ellipse 40% 36% at 50% 52%, #c45a2a 0 50%, var(--plate) 53% 80%, #241d1a 84%),#241d1a;"></div>
  <div class="vrule" style="left:312px;top:560px;height:124px;"></div>
  <div class="rule" style="left:248px;top:684px;width:65px;"></div>
  <div class="doodle" role="img" aria-label="Line drawing of a mushroom" style="left:314px;top:516px;width:42px;height:44px;"></div>
  <div class="doodle" role="img" aria-label="Line drawing of small mushrooms" style="left:326px;top:610px;width:42px;height:30px;"></div>

  <!-- Penne Arrabbiata -->
  <section class="dish" style="left:364px;top:517px;width:260px;">
    <h2 class="dish-name">PENNE ARRABBIATA | <span class="ar">بيني أرابياتا</span></h2>
    <p class="dish-copy" style="margin-top:13px;">Penne with spicy tomato sauce &amp;<br>fresh basil&nbsp; 27<br>with chicken 37, with shrimp 42</p>
    <p class="dish-ar" style="margin-top:15px;">بيني مع صلصة الطماطم الحارقة<br>والريحان الطازج 29<br>مع الدجاج 39، مع الجمبري 44</p>
  </section>
  <div class="rule" style="left:346px;top:684px;width:98px;"></div>
  <div class="rule" style="left:540px;top:684px;width:98px;"></div>

  <!-- Penne ala Rosa -->
  <section class="dish" style="left:52px;top:714px;width:260px;">
    <h2 class="dish-name">PENNE ALA ROSA | <span class="ar">بيني ألا روزا</span></h2>
    <p class="dish-copy small" style="margin-top:12px;">Penne with tomato &amp; cream sauce &amp; fresh<br>basil&nbsp; 29<br>with chicken 39, with shrimp 44</p>
    <p class="dish-ar small" style="margin-top:12px;">بيني مع صلصة الطماطم والكريمة والريحان<br>الطازج 32<br>مع الدجاج 42، مع الجمبري</p>
  </section>
  <div class="doodle" role="img" aria-label="Line drawing of a cheese wedge" style="left:316px;top:696px;width:56px;height:44px;"></div>
  <div class="doodle" role="img" aria-label="Line drawing of garlic" style="left:316px;top:796px;width:44px;height:48px;"></div>

  <!-- photo: baked penne -->
  <div class="photo" role="img" aria-label="Photo of baked penne with broccoli and melted cheese and garlic bread" style="left:390px;top:718px;width:198px;height:130px;background:radial-gradient(ellipse 44% 40% at 58% 55%, #e9e2c8 0 40%, #9aa868 58%, #efeae2 70%, #b98a5c 86%),#b98a5c;"></div>
  <div class="vrule" style="left:376px;top:716px;height:144px;"></div>
  <div class="rule" style="left:376px;top:860px;width:136px;"></div>
  <svg class="abs" style="left:600px;top:700px;" width="30" height="176" viewBox="0 0 30 176" aria-hidden="true">
    <path d="M14 2 C2 30, 26 50, 12 88 C2 118, 26 140, 14 174" fill="none" stroke="#d9d9d9" stroke-width="1"/>
  </svg>

  <!-- Spaghetti Meatballs -->
  <section class="dish" style="left:56px;top:880px;width:240px;">
    <h2 class="dish-name">SPAGHETTI MEATBALLS |<br><span class="ar">سباجيتي مع كرات اللحم</span></h2>
    <p class="dish-copy" style="margin-top:11px;">Italian style meatballs served with<br>marinara sauce and spaghetti pasta<br>37</p>
    <p class="dish-ar" style="margin-top:16px;">مكرونة السباجيتي مع كرات اللحم<br>بالتتبيلة الإيطالية يعلوها صوص<br>طماطم الماريناراا الغني و جبنة<br>البارميجان الإيطالية المبشورة<br>37</p>
  </section>
  <div class="doodle" role="img" aria-label="Line drawing of a bell pepper" style="left:304px;top:876px;width:36px;height:40px;"></div>
  <div class="doodle" role="img" aria-label="Line drawing of a wheat stalk" style="left:324px;top:940px;width:40px;height:72px;"></div>

  <!-- Baked Penne -->
  <section class="dish" style="left:378px;top:880px;width:224px;">
    <h2 class="dish-name">BAKED PENNE | <span class="ar">بيني بالفرن</span></h2>
    <p class="dish-copy" style="margin-top:30px;">Penne pasta, creamy spinach &amp;<br>mushroom sauce, brocoli, chicken,<br>topped with mozzarella cheese&nbsp; 39<br>with Shrimp&nbsp; 49</p>
    <p class="dish-ar" style="margin-top:16px;">بيني مع كريمة السبانخ والمشروم،<br>بروكولي، أوصال الدجاج ومغطاة<br>بالموزاريلا السائحة 39<br>مع الجمبري 49</p>
  </section>

  <!-- bottom divider -->
  <div class="rule" style="left:0;top:1130px;width:670px;"></div>
  <div class="doodle" role="img" aria-label="Line drawing of a rolling pin" style="left:248px;top:1120px;width:192px;height:20px;opacity:.9;"></div>

</main>
</body>
</html>
```